Meadow Builders Needs a Website!

Single page (plus contact form) website for small home remodeling company. He's got a few pictures he'd like on the site and needs some basic text. He likes clean, simple designs and is "more traditional" in his stylistic preferences. Most of his business comes from word-of-mouth advertising and so the site is just something he needs for people to feel more comfortable with his business.

Target Market(s)

People who want to remodel their homes

Coding

Coded - Design and coding required

Number of Pages Required

2 page

Requirements
Must have
• Main page to include some or all of the attached images, contact page. Neutral colors. Old domain: lindcroftmeadowbuild.com New domain: qm-ventureworks.com You can pull text from the old site or update it.
Should not have
• No loud colors/loud visual elements

```html
<!DOCTYPE html>
<html lang="en">
<head>
<meta charset="utf-8">
<title>Lindcroft Meadow Homes</title>
<link href="https://fonts.googleapis.com/css2?family=Montserrat:wght@400;500;600;700&display=swap" rel="stylesheet">
<style>
:root{
  --brown:#3b1410;
  --orange:#e07a2b;
  --ink:#222;
  --muted:#666;
  --white:#fff;
  --line:#d9d9d9;
}
*{box-sizing:border-box;margin:0;padding:0}
html,body{width:1200px;height:3158px;overflow:hidden;background:#fff}
body{font-family:'Montserrat',sans-serif;color:var(--ink)}
a{color:inherit;text-decoration:none}
.page{width:1200px;height:3158px;position:relative}

/* header */
.site-header{height:70px;display:flex;align-items:stretch;background:#fff}
.brand{width:246px;background:var(--brown);display:flex;align-items:center;justify-content:center;gap:14px;color:#fff;font-weight:700;font-size:16px;line-height:1.1;text-align:center}
.brand-mark{width:26px;height:26px;border:2px solid var(--orange)}
.main-nav{flex:1;display:flex;align-items:center;gap:38px;padding-left:44px;font-size:12px;font-weight:500}
.main-nav .active{color:var(--orange);border-bottom:1px solid var(--orange);padding-bottom:3px}
.social{display:flex;gap:14px;align-items:center;margin-right:28px}
.social span{width:12px;height:12px;border-radius:50%;border:1.5px solid #333;display:block}
.call-box{width:210px;background:var(--orange);color:#fff;font-weight:700;font-size:14px;display:flex;flex-direction:column;justify-content:center;align-items:center;letter-spacing:1px;line-height:1.7}

/* hero */
.hero{height:510px;position:relative;background:linear-gradient(120deg,#3a2a20 0%,#6b5444 35%,#8a7664 55%,#4a3a2e 80%,#2c2119 100%);display:flex;flex-direction:column;align-items:center;justify-content:center;text-align:center}
.hero h1{color:#fff;font-size:74px;font-weight:700;line-height:1.15;text-shadow:0 2px 10px rgba(0,0,0,.35);margin-top:10px}
.btn{display:inline-block;background:var(--orange);color:#fff;font-size:13px;font-weight:500;padding:12px 26px;letter-spacing:.3px}
.hero .btn{margin-top:26px}

/* about */
.about{height:380px;display:flex;align-items:center;gap:80px;padding:0 100px}
.about-photo{position:relative;width:420px;height:280px;flex:none}
.about-photo .shadow-block{position:absolute;left:26px;top:26px;width:420px;height:280px;background:var(--brown)}
.about-photo .photo{position:absolute;inset:0;background:linear-gradient(135deg,#c9b39a,#8c7660 45%,#e6dccd 75%,#a18c76);border:1px solid #eee}
.about-copy h2{font-size:28px;font-weight:600;margin-bottom:20px}
.about-copy p{font-size:13px;line-height:1.8;color:var(--muted);max-width:470px}
.about-copy .btn{margin-top:28px;font-size:11px;padding:9px 24px}

/* tinker */
.tinker{height:480px;background:var(--brown);color:#fff;text-align:center;padding-top:46px}
.section-title{font-size:28px;font-weight:600;letter-spacing:.3px}
.rule{width:290px;height:2px;background:#fff;margin:18px auto 0}
.rule.orange{width:150px;background:var(--orange)}
.cards{display:flex;justify-content:center;gap:100px;margin-top:78px}
.card{position:relative;width:262px;height:318px;background:#fff;color:var(--ink);text-align:left;padding:108px 28px 0}
.card .tab{position:absolute;left:-14px;top:16px;background:var(--orange);color:#fff;font-size:13px;padding:12px 24px 12px 24px;border-radius:0 22px 22px 0;min-width:150px}
.card .icon{position:absolute;left:50%;top:76px;transform:translateX(-50%);width:60px;height:56px;border:1.5px solid var(--orange);border-radius:8px}
.card p{font-size:13px;line-height:1.85;margin-top:36px}
.card .more{display:block;color:var(--orange);font-size:11px;margin-top:16px}
.card svg{position:absolute;right:-12px;bottom:-12px}

/* services */
.services{height:440px;display:flex;align-items:center;padding:0 130px;gap:110px}
.services-copy{width:430px}
.services-copy h2{font-size:24px;font-weight:600}
.services-copy .rule{margin:10px 0 24px;width:150px}
.services-copy p{font-size:12.5px;line-height:1.65;color:var(--muted);margin-bottom:14px}
.thumbs{display:flex;gap:56px;margin-top:22px}
.thumbs span{width:56px;height:56px;border-radius:50%;background:linear-gradient(135deg,#7d6a5a,#d8d0c6);box-shadow:2px 3px 6px rgba(0,0,0,.25)}
.compare{position:relative;width:312px;height:312px}
.compare .before{height:156px;background:linear-gradient(160deg,#8e7c68,#5a4536 60%,#c4b8a6)}
.compare .after{height:156px;background:linear-gradient(160deg,#e8e6e2,#a7a4a0 55%,#5b524a)}
.compare .label{position:absolute;left:0;right:0;background:rgba(60,30,20,.55);color:#fff;text-align:center;font-size:15px;font-weight:600;padding:4px 0}
.compare .l1{top:130px}.compare .l2{bottom:0}
.arrows{position:absolute;right:-40px;top:186px;display:flex;flex-direction:column;gap:14px}
.arrows span{width:26px;height:26px;border-radius:50%;border:1px solid #ccc;font-size:12px;display:flex;align-items:center;justify-content:center;color:#555}
.counter{position:absolute;right:-48px;bottom:0;font-size:11px;background:#eee;padding:4px 8px}

/* blog */
.blog{height:560px;background:var(--brown);color:#fff;text-align:center;padding-top:54px}
.posts{display:flex;justify-content:center;gap:72px;margin-top:56px}
.post{width:280px}
.post .img{height:148px;width:272px;margin:0 auto;background:linear-gradient(135deg,#9a8f86,#5d544c 50%,#c7bfb4)}
.post:nth-child(3) .img{background:linear-gradient(135deg,#2e4a78,#8b857c 50%,#5b4a3c)}
.post .date{font-size:10px;margin-top:20px}
.post h3{font-size:15px;font-weight:500;margin-top:12px}
.post p{font-size:10.5px;line-height:1.35;color:#d9c9c4;margin:16px auto 0;width:228px}
.post .read{display:block;font-size:10.5px;margin-top:38px}
.btn.light{background:#fff;color:var(--ink);font-size:11px;padding:9px 30px;margin-top:58px}

/* testimonial */
.testimonial{height:440px;text-align:center;padding-top:46px}
.testimonial .section-title{color:var(--ink)}
.quotes{display:flex;justify-content:center;gap:86px;margin-top:50px}
.quote{width:306px;height:226px;background:#fff;box-shadow:0 2px 14px rgba(0,0,0,.18);padding:24px 30px 0}
.stars{color:var(--orange);font-size:18px;letter-spacing:3px}
.quote p{font-size:12px;line-height:1.6;margin-top:10px}
.avatar{width:48px;height:48px;border-radius:50%;margin:10px auto 0;background:linear-gradient(135deg,#cfc6bc,#6e6358)}
.quote .name{font-size:11px;font-weight:500;margin-top:8px}
.quote .place{font-size:10px;color:var(--orange);margin-top:6px}
.testimonial .btn{margin-top:38px;font-size:10.5px;padding:8px 28px}

/* footer */
.site-footer{height:288px;background:var(--brown);color:#fff;padding:46px 66px 0}
.footer-cols{display:flex;gap:0}
.footer-cols>div{flex:none}
.f-about{width:294px}
.f-about h3{font-size:26px;font-weight:500}
.f-about p{font-size:11.5px;line-height:1.65;margin-top:14px;width:240px}
.f-social{display:flex;gap:34px;margin:18px 0 0 18px}
.f-social span{width:14px;height:14px;border-radius:50%;border:1.5px solid #fff;display:block}
.f-list{width:236px}
.f-list h4{font-size:18px;font-weight:500;margin-top:6px}
.f-list ul{list-style:none;margin-top:14px}
.f-list li{font-size:11.5px;line-height:1;margin-bottom:11px;position:relative;padding-left:30px}
.f-list li::before{content:"";position:absolute;left:0;top:2px;width:6px;height:6px;border-radius:50%;background:var(--orange)}
.f-call h4{font-size:21px;font-weight:400;margin-top:4px}
.f-call .phone{color:var(--orange);font-size:21px;margin-top:4px}
.f-call .row{display:flex;align-items:center;gap:22px;font-size:18px;margin-top:22px;padding-left:8px}
.footer-bottom{border-top:1px solid rgba(255,255,255,.35);margin-top:36px;padding-top:16px;text-align:center;font-size:12px}
</style>
</head>
<body>
<div class="page">

<header class="site-header">
  <div class="brand"><span class="brand-mark"></span><span>Meadow<br>Builders</span></div>
  <nav class="main-nav">
    <a class="active" href="#">Home</a><a href="#">Services</a><a href="#">Projects</a><a href="#">Blogs</a><a href="#">About us</a><a href="#">Contacts us</a>
  </nav>
  <div class="social"><span></span><span></span><span></span><span></span></div>
  <div class="call-box"><span>CALL US TODAY !</span><span>555-014-2290</span></div>
</header>

<section class="hero" role="img" aria-label="Photo of a warm, sunlit living room with bookshelves, desk and a person by the windows">
  <h1>Welcome to Lindcroft<br>Meadow Homes</h1>
  <a class="btn" href="#">MAKE AN APPOINMENTS</a>
</section>

<section class="about">
  <div class="about-photo">
    <div class="shadow-block"></div>
    <div class="photo" role="img" aria-label="Photo of a remodeled open living room with staircase"></div>
  </div>
  <div class="about-copy">
    <h2>ABOUT US</h2>
    <p>When you want affordable, quality home construction services; think of us to do the job.<br>
    Since 1981 Walter Brennick has built and remodeled over 400 homes and businesses. Let us be your contractor for the next project you start.<br>
    When quality, value and personal attention to detail are important With over 20 years experience in residential and commercial construction, you can trust your project to Lindcroft Meadow Homes</p>
    <a class="btn" href="#">LEARN MORE</a>
  </div>
</section>

<section class="tinker">
  <h2 class="section-title">DON'T TINKER AROUND</h2>
  <div class="rule"></div>
  <div class="cards">
    <article class="card">
      <span class="tab">PARTNERSHIP</span>
      <span class="icon" role="img" aria-label="Handshake icon"></span>
      <p>I Have Built My Business With A Partnership Of Clients, Employees, Subcontractors</p>
      <a class="more" href="#">LEARN MORE</a>
      <svg width="84" height="84" viewBox="0 0 84 84"><polygon points="84,0 84,84 0,84" fill="var(--orange)"/><text x="62" y="74" fill="#fff" font-size="24" font-family="Montserrat,sans-serif">1</text></svg>
    </article>
    <article class="card">
      <span class="tab">CONSTRUCTION</span>
      <span class="icon" role="img" aria-label="House construction icon"></span>
      <p>I Have Deep "Hands On" History In Construction From Foundations To Final Finishing Touches.</p>
      <a class="more" href="#">LEARN MORE</a>
      <svg width="84" height="84" viewBox="0 0 84 84"><polygon points="84,0 84,84 0,84" fill="var(--orange)"/><text x="60" y="74" fill="#fff" font-size="24" font-family="Montserrat,sans-serif">2</text></svg>
    </article>
    <article class="card">
      <span class="tab">SUPPLIER</span>
      <span class="icon" role="img" aria-label="Supplier tools icon"></span>
      <p>We Cultivate Suppliers Who Deliver Quality Materials On Time And Without Damage.</p>
      <a class="more" href="#">LEARN MORE</a>
      <svg width="84" height="84" viewBox="0 0 84 84"><polygon points="84,0 84,84 0,84" fill="var(--orange)"/><text x="60" y="74" fill="#fff" font-size="24" font-family="Montserrat,sans-serif">3</text></svg>
    </article>
  </div>
</section>

<section class="services">
  <div class="services-copy">
    <h2>OUR SERVICES</h2>
    <div class="rule orange"></div>
    <p>First things first, if you're investing in your kitchen, it should be a reflection of you and your lifestyle. Begin by thinking about how you use your kitchen, and what you'll need and want from it on a daily basis.</p>
    <p>Before you dive into meeting with a contractor, you need to take a evaluate how you currently use your kitchen, and what you'd like to get out of it. It's easy to leave things out, so we've created an easy worksheet guide to help you think about the current activities</p>
    <div class="thumbs">
      <span role="img" aria-label="Project photo thumbnail"></span><span role="img" aria-label="Project photo thumbnail"></span><span role="img" aria-label="Project photo thumbnail"></span><span role="img" aria-label="Project photo thumbnail"></span>
    </div>
  </div>
  <div class="compare">
    <div class="before" role="img" aria-label="Before photo of a gutted kitchen under renovation"></div>
    <div class="after" role="img" aria-label="After photo of a finished white kitchen"></div>
    <span class="label l1">Before</span>
    <span class="label l2">After</span>
    <div class="arrows"><span>&#8250;</span><span>&#8249;</span></div>
    <span class="counter">6</span>
  </div>
</section>

<section class="blog">
  <h2 class="section-title">OUR BLOG</h2>
  <div class="rule orange"></div>
  <div class="posts">
    <article class="post">
      <div class="img" role="img" aria-label="Photo of a remodeled bathroom with glass shower"></div>
      <div class="date">28 /09 /2020</div>
      <h3>Small Bathroom Ideas</h3>
      <p>sed ut perspiciatis, unde omnis iste natus error sit voluptatem accusantium doloremque laudantium, totam rem aperiam eaque ipsa, quae ab illo inventore veritatis et quasi architecto</p>
      <a class="read" href="#">READ FULL ARTICLE</a>
    </article>
    <article class="post">
      <div class="img" role="img" aria-label="Photo of an open living room with staircase"></div>
      <div class="date">28 /09 /2020</div>
      <h3>Elegant Floating Vanities</h3>
      <p>sed ut perspiciatis, unde omnis iste natus error sit voluptatem accusantium doloremque laudantium, totam rem aperiam eaque ipsa, quae ab illo inventore veritatis et quasi architecto</p>
      <a class="read" href="#">READ FULL ARTICLE</a>
    </article>
    <article class="post">
      <div class="img" role="img" aria-label="Photo of a kitchen with blue walls and steel appliances"></div>
      <div class="date">28 /09 /2020</div>
      <h3>Small Bathroom Ideas</h3>
      <p>sed ut perspiciatis, unde omnis iste natus error sit voluptatem accusantium doloremque laudantium, totam rem aperiam eaque ipsa, quae ab illo inventore veritatis et quasi architecto</p>
      <a class="read" href="#">READ FULL ARTICLE</a>
    </article>
  </div>
  <a class="btn light" href="#">LEARN MORE</a>
</section>

<section class="testimonial">
  <h2 class="section-title">TESTIMONIAL</h2>
  <div class="rule orange"></div>
  <div class="quotes">
    <blockquote class="quote">
      <div class="stars">★★★★★</div>
      <p>lorem ipsum dolor sit amet, consectetur adipiscing elit. nulla sed cum nunc, egestas placerat vulputate id vitae. a id pellentesque suspendisse tortor mi elementum interdum mauris venenatis.</p>
      <div class="avatar" role="img" aria-label="Client portrait"></div>
      <div class="name">DANIEL HOLLIS</div>
      <div class="place">OAKRIDGE.MN</div>
    </blockquote>
    <blockquote class="quote">
      <div class="stars">★★★★★</div>
      <p>lorem ipsum dolor sit amet, consectetur adipiscing elit. nulla sed cum nunc, egestas placerat vulputate id vitae. a id pellentesque suspendisse tortor mi elementum interdum mauris venenatis.</p>
      <div class="avatar" role="img" aria-label="Client portrait"></div>
      <div class="name">DANIEL HOLLIS</div>
      <div class="place">OAKRIDGE.MN</div>
    </blockquote>
    <blockquote class="quote">
      <div class="stars">★★★★★</div>
      <p>lorem ipsum dolor sit amet, consectetur adipiscing elit. nulla sed cum nunc, egestas placerat vulputate id vitae. a id pellentesque suspendisse tortor mi elementum interdum mauris venenatis.</p>
      <div class="avatar" role="img" aria-label="Client portrait"></div>
      <div class="name">DANIEL HOLLIS</div>
      <div class="place">OAKRIDGE.MN</div>
    </blockquote>
  </div>
  <a class="btn" href="#">LEARN MORE</a>
</section>

<footer class="site-footer">
  <div class="footer-cols">
    <div class="f-about">
      <h3>Lindcroft Meadow</h3>
      <p>Since 1981 Walter Brennick has built and remodeled over 400 homes and businesses. Let us be your contractor for the next project you start.</p>
      <div class="f-social"><span></span><span></span><span></span><span></span></div>
    </div>
    <div class="f-list">
      <h4>SERVICE</h4>
      <ul><li>Addition</li><li>New Construction</li><li>historic renovations</li><li>painting</li><li>gutters</li><li>electric</li></ul>
    </div>
    <div class="f-list">
      <h4>CUSTOMER CARE</h4>
      <ul><li>About Us</li><li>Our Services</li><li>blog</li><li>Contact Us</li><li>Contact Us</li></ul>
    </div>
    <div class="f-call">
      <h4>Call Now For Services!</h4>
      <div class="phone">555-014-2290</div>
      <div class="row"><svg width="22" height="16" viewBox="0 0 22 16" fill="none" stroke="#fff" stroke-width="1.4"><rect x="1" y="1" width="20" height="14"/><polyline points="1,1 11,9 21,1"/></svg>Email Us</div>
      <div class="row"><svg width="18" height="22" viewBox="0 0 18 22" fill="none" stroke="#fff" stroke-width="1.4"><path d="M9 21C9 21 2 13 2 8a7 7 0 0 1 14 0c0 5-7 13-7 13z"/><circle cx="9" cy="8" r="2.5"/></svg>Get Direction</div>
    </div>
  </div>
  <div class="footer-bottom">Lindcroft Meadow © 2021 All Rights Reserved. Terms of Use and Privacy Policy</div>
</footer>

</div>
</body>
</html>
```